Graphic Design for a 3 Banner Tradeshow Setup

We are a Pipe Restoration company that specializes in trenchless pipelining. We need a design for a 3 banner setup to use at tradeshows. See attached "banner specs" for sizing - note the 48" x 92" will be in between the two 36" x 92" banners. See attached "Mock-Up" of information each banner needs and utilize the color scheme of the banners we already have in the "both DWM banners" AI file attached. The final designs should communicate what we do and attract people into our booth. We would like to have graphics of realistic pipes for a before (dirty pipe), after cleaning pipe, and lined pipe - see example of "pipe pictures" attached. I'm not sure if this is something you can generate or if we will need to find images of our own to send. Also, see attached "screenshot-process" to see similar images we would like to use to showcase the process.
Target Market(s)
Homeowners, Property Managers, HOA Communities, Healthcare Facilities & Hospitals, and commercial properties
Industry/Entity Type
Trenchless Pipelining
Look and feel

```html
<!DOCTYPE html>
<html lang="en">
<head>
<meta charset="utf-8">
<title>DWM Tradeshow Banners</title>
<link rel="stylesheet" href="https://fonts.googleapis.com/css2?family=Russo+One&family=Saira:ital,wght@1,800&family=Barlow:wght@400;500&display=swap">
<style>
  :root {
    --navy: #0f1a33;
    --navy-mid: #1b3a7a;
    --blue: #1389d6;
    --blue-bright: #19a7e8;
    --sky: #e7f1fa;
    --panel-edge: #1a5fb4;
    --ink: #121a2c;
    --white: #ffffff;
    --stage: #e4e5e7;
  }
  * { box-sizing: border-box; margin: 0; padding: 0; }
  html, body { width: 1200px; height: 982px; overflow: hidden; background: var(--stage); }
  body { position: relative; font-family: "Barlow", sans-serif; }

  .banner { position: absolute; top: 61px; height: 860px; overflow: hidden; }
  .banner--side { width: 336px; background: linear-gradient(180deg, var(--navy) 0%, var(--navy) 28%, #14407f 60%, var(--blue) 85%, var(--blue-bright) 100%); }
  .banner--left { left: 20px; }
  .banner--right { left: 845px; }
  .banner--center { left: 376px; width: 449px; background: var(--white); }

  /* brand */
  .brand { position: absolute; top: 42px; left: 0; right: 0; text-align: center; color: var(--white); }
  .brand__row { display: flex; justify-content: center; align-items: center; gap: 10px; }
  .brand__mark { width: 40px; height: 40px; border-radius: 6px; background: linear-gradient(160deg, var(--blue-bright), var(--navy-mid)); }
  .brand__name { font-family: "Russo One", sans-serif; font-size: 64px; line-height: 1; letter-spacing: 2px; }
  .brand__tagline { font-family: "Russo One", sans-serif; font-size: 10.5px; letter-spacing: 3.2px; margin-top: 6px; }

  /* panel */
  .panel { position: absolute; top: 158px; left: 30px; right: 30px; height: 578px; border-radius: 22px; border: 2px solid var(--panel-edge);
           background: radial-gradient(ellipse at 50% 45%, #ffffff 0%, var(--sky) 55%, #bcd9ee 100%); }
  .panel__tab { position: absolute; top: -10px; left: 50%; transform: translateX(-50%); width: 206px; height: 38px; border-radius: 0 0 18px 18px;
                background: linear-gradient(180deg, var(--blue) 0%, var(--navy-mid) 100%); color: var(--white);
                font-family: "Russo One", sans-serif; font-size: 20px; display: flex; align-items: center; justify-content: center; }
  .icon-box { width: 64px; height: 64px; border-radius: 6px; flex: none;
              background: linear-gradient(160deg, var(--blue-bright), var(--navy-mid)); display: flex; align-items: center; justify-content: center;
              box-shadow: 0 2px 4px rgba(15,26,51,.35); }
  .icon-box svg { width: 44px; height: 44px; fill: none; stroke: var(--white); stroke-width: 2; stroke-linecap: round; stroke-linejoin: round; }

  .assess-list { list-style: none; position: absolute; top: 44px; bottom: 18px; left: 0; right: 0; display: flex; flex-direction: column; justify-content: space-between; align-items: center; }
  .assess-item { display: flex; flex-direction: column; align-items: center; gap: 6px; }
  .assess-item__label { font-family: "Russo One", sans-serif; font-size: 17px; line-height: 1.05; color: var(--ink); text-align: center; letter-spacing: .5px; }

  .fix-list { list-style: none; position: absolute; top: 48px; bottom: 18px; left: 22px; right: 10px; display: flex; flex-direction: column; justify-content: space-between; }
  .fix-item { display: flex; align-items: center; gap: 14px; }
  .fix-item .icon-box { width: 60px; height: 60px; }
  .fix-item__label { font-family: "Russo One", sans-serif; font-size: 17px; line-height: 1.05; color: var(--ink); letter-spacing: .5px; }

  .cta { position: absolute; top: 758px; left: 0; right: 0; text-align: center; color: var(--white);
         font-family: "Saira", sans-serif; font-style: italic; font-weight: 800; font-size: 19px; line-height: 1.15; text-transform: uppercase; }
  .phone-pill { position: absolute; top: 812px; left: 32px; right: 32px; height: 34px; border-radius: 17px; background: var(--navy);
                border: 2px solid var(--white); color: var(--white); font-family: "Russo One", sans-serif; font-size: 21px;
                display: flex; align-items: center; justify-content: center; letter-spacing: 1px; }

  /* center */
  .headline { position: absolute; top: 22px; left: 0; right: 0; text-align: center; font-family: "Russo One", sans-serif; }
  .headline__big { font-size: 88px; line-height: 1; background: linear-gradient(180deg, #1d5fb8, #0f8fd4); -webkit-background-clip: text; background-clip: text; color: transparent; letter-spacing: 3px; }
  .headline__sub { font-size: 43px; line-height: 1; color: var(--navy-mid); margin-top: 4px; }
  .promise { position: absolute; top: 155px; left: 0; right: 0; height: 125px; background: linear-gradient(180deg, var(--blue-bright) 0%, var(--blue) 40%, var(--navy-mid) 100%);
             color: var(--white); text-align: center; font-family: "Russo One", sans-serif; padding-top: 18px; }
  .promise__lead { font-size: 16px; letter-spacing: .5px; }
  .promise__main { font-size: 28px; line-height: 1.1; margin-top: 6px; }

  .process { position: absolute; top: 285px; left: 0; width: 449px; height: 440px; }
  .process__ring { position: absolute; top: 0; left: 0; }
  .visual { position: absolute; border-radius: 4px; }
  .visual--camera { left: 110px; top: 10px; width: 170px; height: 72px; background: linear-gradient(160deg, #3a3d44, #7d5a3c 50%, #3b4048); transform: rotate(14deg); }
  .visual--clean { left: 32px; top: 146px; width: 174px; height: 64px; background: linear-gradient(90deg, #4a4c52, #6f6a4a 30%, #b9bcc2 60%, #5c6068); transform: rotate(4deg); }
  .visual--liner { left: 55px; top: 292px; width: 170px; height: 58px; background: linear-gradient(90deg, #3e4249, #1f8fd9 55%, #2aa7e4); transform: rotate(-14deg); }
  .visual--lined { left: 262px; top: 340px; width: 140px; height: 64px; background: linear-gradient(90deg, #163f8a, #1a76cf 60%, #2c9be3); transform: rotate(-22deg); }
  .visual--compare { left: 238px; top: 58px; width: 211px; height: 250px; border-radius: 50% 0 0 50% / 40% 0 0 40%; overflow: hidden;
                     background: linear-gradient(180deg, #6b4a2b 0%, #8a5a2e 45%, #4aa7df 52%, #1e78c5 100%); }
  .visual__tag { position: absolute; left: 56px; color: var(--white); font-family: "Russo One", sans-serif; font-size: 12px; }
  .step-num { position: absolute; width: 32px; height: 32px; border-radius: 50%; background: linear-gradient(160deg, #1f6cc4, var(--navy-mid));
              border: 2px solid var(--white); box-shadow: 0 0 0 1px #9fb6d4; color: var(--white); font-family: "Russo One", sans-serif; font-size: 18px;
              display: flex; align-items: center; justify-content: center; }
  .step-text { position: absolute; font-size: 10.5px; line-height: 1.2; color: #1c1c1c; }

  .contact { position: absolute; top: 744px; left: 20px; right: 20px; bottom: 0; border-radius: 14px 14px 0 0; background: linear-gradient(180deg, #111 0%, #2a2a2c 100%); text-align: center; }
  .contact__tab { position: absolute; top: 727px; left: 45px; right: 48px; height: 31px; border-radius: 4px; background: var(--blue-bright); color: var(--white);
                  font-family: "Barlow", sans-serif; font-weight: 500; font-size: 14.5px; display: flex; align-items: center; justify-content: center; letter-spacing: .3px; }
  .contact__web { margin-top: 30px; font-family: "Russo One", sans-serif; font-size: 19px; color: var(--blue-bright); letter-spacing: 1px; }
  .contact__phone { margin-top: 6px; font-family: "Russo One", sans-serif; font-size: 32px; color: var(--white); letter-spacing: 1px; }
</style>
</head>
<body>

<!-- Left banner -->
<section class="banner banner--side banner--left">
  <header class="brand">
    <div class="brand__row"><span class="brand__mark"></span><span class="brand__name">DWM</span></div>
    <div class="brand__tagline">DURABLE WATER MAINS</div>
  </header>
  <div class="panel">
    <div class="panel__tab">WE ASSESS</div>
    <ul class="assess-list">
      <li class="assess-item">
        <span class="icon-box"><svg viewBox="0 0 44 44"><rect x="8" y="12" width="12" height="10" rx="2"/><path d="M14 22v12M26 8v26a4 4 0 0 0 8 0V8"/><circle cx="14" cy="17" r="2"/></svg></span>
        <span class="assess-item__label">CCTV PIPE<br>INVESTIGATION</span>
      </li>
      <li class="assess-item">
        <span class="icon-box"><svg viewBox="0 0 44 44"><path d="M4 14h8l6 4 6-4h6l10 2v10l-10 8-8-4-6 2-6-6H4z"/><path d="M18 26l4 4M22 24l4 4"/></svg></span>
        <span class="assess-item__label">SCOPE<br>DEVELOPMENT</span>
      </li>
      <li class="assess-item">
        <span class="icon-box"><svg viewBox="0 0 44 44"><rect x="8" y="5" width="22" height="34" rx="3"/><rect x="12" y="9" width="14" height="7"/><path d="M13 21h2M19 21h2M13 27h2M19 27h2M13 33h2M19 33h2"/><circle cx="33" cy="30" r="6"/><path d="M33 26v8"/></svg></span>
        <span class="assess-item__label">BUDGETARY<br>EVALUATION</span>
      </li>
      <li class="assess-item">
        <span class="icon-box"><svg viewBox="0 0 44 44"><circle cx="22" cy="20" r="10"/><path d="M22 20l5-4M15 27l-9 9"/><path d="M34 6v30"/></svg></span>
        <span class="assess-item__label">PROJECT<br>OVERSIGHT</span>
      </li>
    </ul>
  </div>
  <p class="cta">Call today for all<br>your plumbing needs!</p>
  <div class="phone-pill">1-800-555-0147</div>
</section>

<!-- Center banner -->
<section class="banner banner--center">
  <header class="headline">
    <div class="headline__big">PIPE</div>
    <div class="headline__sub">PROBLEMS?</div>
  </header>
  <div class="promise">
    <div class="promise__lead">WE HELP FIX PIPE PROBLEMS</div>
    <div class="promise__main">WITHOUT HAVING TO<br>TEAR UP YOUR BUIDLING</div>
  </div>

  <div class="process">
    <svg class="process__ring" width="449" height="440" viewBox="0 0 449 440">
      <circle cx="282" cy="200" r="165" fill="none" stroke="#dde1e6" stroke-width="9"/>
    </svg>
    <div class="visual visual--camera" role="img" aria-label="Cutaway of a pipe with debris and roots inspected by a sewer camera"></div>
    <div class="visual visual--clean" role="img" aria-label="Cutaway of a pipe being mechanically cleaned by a cutting tool"></div>
    <div class="visual visual--liner" role="img" aria-label="Cutaway of a pipe with a blue CIPP liner and inflated bladder"></div>
    <div class="visual visual--lined" role="img" aria-label="Finished pipe with a blue structural liner inside"></div>
    <div class="visual visual--compare" role="img" aria-label="Photo of a corroded pipe with roots before and a smooth blue lined pipe after">
      <span class="visual__tag" style="top:108px">BEFORE</span>
      <span class="visual__tag" style="top:146px">AFTER</span>
    </div>

    <span class="step-num" style="left:248px;top:12px">1</span>
    <span class="step-num" style="left:122px;top:101px">2</span>
    <span class="step-num" style="left:113px;top:238px">3</span>
    <span class="step-num" style="left:188px;top:354px">4</span>

    <p class="step-text" style="left:299px;top:13px;width:130px">A sewer camera is used to investigate the pipe to determine condition</p>
    <p class="step-text" style="left:47px;top:98px;width:75px">The Pipe is mechanically cleaned</p>
    <p class="step-text" style="left:22px;top:243px;width:90px">A CIPP Liner is pulled into place and the bladder inflated.</p>
    <p class="step-text" style="left:104px;top:400px;width:150px">After curing the bladder is removed leaving behind a structrial pipe within a pipe</p>
  </div>

  <div class="contact">
    <div class="contact__web">WWW.DWMPIPE.COM</div>
    <div class="contact__phone">1-800-555-0147</div>
  </div>
  <div class="contact__tab">CALL TODAY FOR ALL YOUR PIPE RESTORATION</div>
</section>

<!-- Right banner -->
<section class="banner banner--side banner--right">
  <header class="brand">
    <div class="brand__row"><span class="brand__mark"></span><span class="brand__name">DWM</span></div>
    <div class="brand__tagline">DURABLE WATER MAINS</div>
  </header>
  <div class="panel">
    <div class="panel__tab">WE FIX</div>
    <ul class="fix-list">
      <li class="fix-item">
        <span class="icon-box"><svg viewBox="0 0 44 44"><path d="M8 8h8v18a6 6 0 0 0 12 0v-4h10v-6H24v8"/><circle cx="20" cy="30" r="1"/></svg></span>
        <span class="fix-item__label">SLOW<br>DRAINS</span>
      </li>
      <li class="fix-item">
        <span class="icon-box"><svg viewBox="0 0 44 44"><path d="M10 6v22M16 6v22M22 10h8a6 6 0 0 1 6 6v10"/><path d="M4 32c4-3 8 3 12 0s8 3 12 0 8 3 12 0M4 38h36"/></svg></span>
        <span class="fix-item__label">WATER<br>BACK - UPS</span>
      </li>
      <li class="fix-item">
        <span class="icon-box"><svg viewBox="0 0 44 44"><path d="M14 6c-3 4 3 6 0 10s3 6 0 10M22 6c-3 4 3 6 0 10s3 6 0 10M30 6c-3 4 3 6 0 10s3 6 0 10"/><ellipse cx="22" cy="32" rx="14" ry="5"/><path d="M8 32v3c0 3 6 5 14 5s14-2 14-5v-3"/></svg></span>
        <span class="fix-item__label">SEWER<br>ODORS</span>
      </li>
      <li class="fix-item">
        <span class="icon-box"><svg viewBox="0 0 44 44"><path d="M4 14h36v10H4zM8 10v18M36 10v18"/><path d="M20 14l2 4-2 3 3 3"/><path d="M22 28c-2 3-2 6 0 6s2-3 0-6z"/></svg></span>
        <span class="fix-item__label">CRACKED<br>PIPES</span>
      </li>
      <li class="fix-item">
        <span class="icon-box"><svg viewBox="0 0 44 44"><path d="M22 24V8M22 14c-4-4-8-2-8 0 4 2 6 2 8 0M22 12c4-4 8-2 8 0-4 2-6 2-8 0"/><path d="M4 22h36v10H4z"/><path d="M22 24l-4 12M22 26l5 10"/></svg></span>
        <span class="fix-item__label">ROOT<br>INTRUSION</span>
      </li>
      <li class="fix-item">
        <span class="icon-box"><svg viewBox="0 0 44 44"><path d="M6 10h26M10 10v12M28 6v8M32 6v8"/><path d="M14 22c-2 3-2 5 0 5s2-2 0-5z"/><path d="M12 38l22-14 4 4-22 14z"/></svg></span>
        <span class="fix-item__label">RECURRING<br>PLUMBING<br>PROBLEMS</span>
      </li>
    </ul>
  </div>
  <p class="cta">Call today for all<br>your plumbing needs!</p>
  <div class="phone-pill">1-800-555-0147</div>
</section>

</body>
</html>
```